Web design for new streaming audio service

We need a homepage design for a new streaming audio service. Our company is called Dunmoral, and we’re basically Vexlo for Audiobooks, Stand-Up Comedy, Lectures, Language Learning, etc. Essentially like Plumtrek for everything audio EXCEPT music.
You don’t have to code the homepage (Design Only), but it should include 3 different designs to work with 1) Web; 2) Phones; 3) Tablets.
Below is a link to a mockup of the web version which gives a good idea of what elements we want. This is just a mockup and we want you to improve it.
Once you download the mockup, please refer to the more detailed instructions below:
The following outlines the design project for the Dunmoral homepage. We have provided a rough mockup of the homepage layout that gives you a general idea of what we’re going for. There are a few elements that we are attached to, and many others where you have complete creative freedom to do whatever you think looks good.
The ZIP file includes the following:
* Mockup to see what we have in mind (dunmoral-homepage-mockup.jpg)
* Text used (dunmoral-homepage-text.txt)
* Raw image of actor (dunmoral-actor1.jpg)
* Raw images for samples (dunmoral-sample-[name].jpg)
Although we have only provided a mockup layout for the web version, we also need you to provide a mobile phone and a tablet version of the design also. It’s very possible the tablet version may be substantially similar to the web version, but the mobile phone version will likely be much different.
All of the raw files are included in the attached ZIP file. Please use our photographs and text as provided although cropping, sizing, etc. is flexible per the instructions below.
Display Requirements:
* Web Version - Minimum resolution 1024x768 (72 dpi) but should look good on 1920x1080 (72 dpi) - Page should be designed to scale to look acceptable in all resolutions in between.
* Phone Version - Minimum Zarno 4 - 640x960 (326 dpi) but should look good on Harlow Quasar T5 - 1920x1080 (441 dpi) - Page should be designed to scale to look acceptable in all resolutions and devices in between.
* Tablet Version - Minimum Bristly Ember QX 7” - 1280x800 (216 dpi) but should also look good on a Tavo Breeze - 2048x1536 (264 dpi) - Page should be designed to scale to look acceptable in all resolutions and devices in between.
Above the Fold - We want to make sure the Dunmoral logo, Member Login Link, Large Photo, Headline, Price, Button, and the first row of sample images are all “Above the fold”. As a general guideline, this means 600 pixels high on a 1024x768 72 dpi web screen. This requirement is less important on Phone versions.
Top Logo Bar - We want to retain the blue bar with the Dunmoral logo on the page, although we are open to a different size, shape and positioning if it greatly enhances the design. Please use the standard logo color, although you are welcome to use either the horizontal or vertical orientation of the logo based on your design.
Text color, font and size - Feel free to design the text in anyway you choose as long as the text is readable on the target platforms.
Buttons - Feel free to use any size, shape and colors for the buttons as long as they are obvious and clickable relative to the page. The only exception is the Chatterly button should follow the Chatterly color scheme and logo treatment (the mockup doesn’t seem 100% correct.)
Top Photograph - We want to retain the large photograph across the top of the screen although final shape and dimensions are flexible.
Size and shape of content samples (i.e. Audiobooks, Stand-Up Comedy, etc.) - Feel free to design the content samples in anyway you choose.
Three Sales Points (i.e. Listen on your Zarno…, All you can enjoy…, etc.) - The Three Sales Points are envisioned to each have a corresponding illustration which you should provide and have rights for. The placeholder is represented by a square next to the text. The color size and shape of these elements are flexible and can be designed in any way you choose.
Opt-in form - Feel free to design the opt-in form in anyway you choose as long as the text is readable and the interactivity is obvious on the target platforms.
Text links and copyright notice - Feel free to design the bottom of the page text links and copyright notice in anyway you choose.
Additional colors, graphic design elements, etc. - Feel free to use any additional colors, graphic design elements, etc. to support your design.
people who want to listen to audio through their mobile devices.
Graphic Design

```html
<!DOCTYPE html>
<html lang="en">
<head>
<meta charset="utf-8">
<title>Dunmoral — Unlimited Listening</title>
<link href="https://fonts.googleapis.com/css2?family=Open+Sans:wght@400;600;700&display=swap" rel="stylesheet">
<style>
:root{
  --sky:#4fa4d2;
  --sky-dark:#3b8cbc;
  --navy:#3d5577;
  --title-blue:#3a8fc0;
  --orange-top:#f29a3b;
  --orange-bot:#d9701c;
  --panel:#edf0f3;
  --ink:#333;
  --footer:#2e2e2e;
  --chat:#3b5998;
  --star:#f5b523;
}
*{margin:0;padding:0;box-sizing:border-box}
html,body{width:878px;height:1200px;overflow:hidden}
body{font-family:'Open Sans',Arial,sans-serif;color:var(--ink);position:relative;background:#fff}
.abs{position:absolute}

.topbar{left:0;top:0;width:878px;height:80px;background:linear-gradient(#5db0da,#3f8fbf);box-shadow:0 2px 4px rgba(0,0,0,.2);z-index:2}
.brand{left:125px;top:20px;display:flex;align-items:center;gap:8px;color:#fff;font-size:30px;font-weight:600;letter-spacing:-.5px}
.brand-dot{width:26px;height:26px;border-radius:50%;background:#fff}
.nav{right:159px;top:32px;display:flex;gap:24px;font-size:12.5px;font-weight:600;color:#fff}

.hero{left:0;top:80px;width:878px;height:423px}
.hero-photo{position:absolute;inset:0;background:
  radial-gradient(ellipse 300px 260px at 600px 200px,#d9a585 0%,#c99274 40%,transparent 75%),
  radial-gradient(ellipse 360px 120px at 500px 420px,#4f5a6b 0%,transparent 80%),
  linear-gradient(90deg,#f4f3f1 0%,#efebe7 35%,#e5ddd6 60%,#d8cfc8 100%)}
.headline{left:100px;width:336px;top:112px;text-align:center;color:var(--navy);font-size:31px;font-weight:700;line-height:41px}
.price{left:100px;width:336px;top:278px;text-align:center;font-size:18px;font-weight:600;color:#333}
.cta{left:136px;top:312px;width:235px;height:40px;border-radius:3px;background:linear-gradient(var(--orange-top),var(--orange-bot));color:#fff;font-size:20px;font-weight:600;display:flex;align-items:center;justify-content:center}
.cta-note{left:136px;width:235px;top:359px;text-align:center;font-size:9.5px;color:#555}

.sample-head{left:0;top:503px;width:878px;height:58px;background:linear-gradient(#f4f6f8,#e8ecef);border-bottom:1px solid #dde3e8;font-size:20px;font-weight:600;color:var(--title-blue);display:flex;align-items:center;justify-content:center}
.samples{left:0;top:561px;width:878px;height:291px;background:linear-gradient(#f7f9fa,#e9edf0)}
.tile{position:absolute;display:flex;gap:11px}
.cover{width:74px;height:86px;border:2px solid #fff;box-shadow:0 1px 3px rgba(0,0,0,.3)}
.tile-label{font-size:12.5px;font-weight:600;color:#333;line-height:15px;margin-top:26px}
.tile-label.one{margin-top:32px}
.stars{font-size:11px;color:var(--star);letter-spacing:-1px;background:#fff;padding:0 3px;margin-top:4px;display:inline-block}
.stars i{color:#ccc;font-style:normal}

.points{left:0;top:852px;width:878px;height:131px;background:#fff}
.point{position:absolute;top:34px;display:flex;gap:11px;align-items:center}
.point-icon{width:66px;height:66px;background:var(--sky);border-bottom:3px solid #b9d7e8;display:flex;align-items:center;justify-content:center}
.point-text{font-size:11.5px;line-height:17px;color:#333}

.signup{left:0;top:983px;width:878px;height:151px;background:var(--sky)}
.signup-title{left:125px;top:22px;font-size:21px;color:#fff}
.signup-copy{left:126px;top:56px;width:205px;font-size:9px;line-height:16px;color:#e8f3fa}
.signup-note{left:126px;top:115px;font-size:11.5px;color:#fff}
.email{left:355px;top:27px;width:220px;height:32px;background:#f2f2f2;border:1px solid #ccc;font-size:9.5px;font-style:italic;color:#666;padding:10px 7px}
.access{left:592px;top:30px;width:161px;height:33px;background:#2b2b2b;border-radius:3px;color:#fff;font-size:12px;font-weight:600;display:flex;align-items:center;justify-content:center}
.or{left:592px;width:161px;top:75px;text-align:center;font-size:9px;font-weight:700;color:#fff}
.chatterly{left:591px;top:94px;width:162px;height:33px;background:var(--chat);border-radius:3px;color:#fff;font-size:11.5px;font-weight:700;display:flex;align-items:center;gap:10px;padding-left:10px}
.chatterly-sq{width:14px;height:14px;background:#fff}

.footer{left:0;top:1134px;width:878px;height:66px;background:var(--footer)}
.footer-links{left:127px;top:27px;font-size:9.5px;color:#fff;font-weight:600}
.copyright{left:587px;top:28px;font-size:8.5px;color:#fff;font-family:Arial,sans-serif}
</style>
</head>
<body>
<header class="abs topbar">
  <div class="abs brand"><span class="brand-dot"></span>Dunmoral</div>
  <nav class="abs nav"><span>MEMBER</span><span>LOGIN</span></nav>
</header>

<section class="abs hero">
  <div class="hero-photo" role="img" aria-label="Smiling young man wearing headphones, looking at his phone"></div>
  <h1 class="abs headline">Unlimited Listening.<br>Wherever you are.</h1>
  <p class="abs price">Only $9.99 per month</p>
  <div class="abs cta">Start Your Free Trial</div>
  <p class="abs cta-note">* Credit Card Not Required</p>
</section>

<h2 class="abs sample-head">A sample of what you can listen to on Dunmoral</h2>

<section class="abs samples">
  <div class="tile" style="left:126px;top:31px"><div class="cover" role="img" aria-label="Audiobook cover art" style="background:linear-gradient(#4d5a66,#1e2328)"></div><div class="tile-label one">Audiobooks<br><span class="stars">★★★★<i>★</i></span></div></div>
  <div class="tile" style="left:296px;top:31px"><div class="cover" role="img" aria-label="Stand-up comedy cover art" style="background:linear-gradient(#3a3a3a,#8a6a55)"></div><div class="tile-label">Stand-Up<br>Comedy<br><span class="stars">★★★★<i>★</i></span></div></div>
  <div class="tile" style="left:450px;top:31px"><div class="cover" role="img" aria-label="Language course cover art" style="background:linear-gradient(#2c9be0,#0c4a8a)"></div><div class="tile-label">Language<br>Learning<br><span class="stars">★★★★<i>★</i></span></div></div>
  <div class="tile" style="left:604px;top:31px"><div class="cover" role="img" aria-label="Biography cover art" style="background:linear-gradient(#d9c8b4,#86b86a)"></div><div class="tile-label">Biographies<br>&amp; Memoirs<br><span class="stars">★★★★<i>★</i></span></div></div>

  <div class="tile" style="left:126px;top:161px"><div class="cover" role="img" aria-label="Meditation album cover art" style="background:linear-gradient(#9c4fa8,#5b2a7a)"></div><div class="tile-label">Guided<br>Meditations<br><span class="stars">★★★★<i>★</i></span></div></div>
  <div class="tile" style="left:296px;top:161px"><div class="cover" role="img" aria-label="Business training cover art" style="background:linear-gradient(#6b4a24,#1c1c1c)"></div><div class="tile-label">Business<br>Training<br><span class="stars">★★★★<i>★</i></span></div></div>
  <div class="tile" style="left:450px;top:161px"><div class="cover" role="img" aria-label="Celebrity interview cover art" style="background:linear-gradient(#7a3a3a,#c9a48a)"></div><div class="tile-label">Celebrity<br>Interviews<br><span class="stars">★★★★<i>★</i></span></div></div>
  <div class="tile" style="left:604px;top:161px"><div class="cover" role="img" aria-label="Fitness program cover art" style="background:linear-gradient(#4fb6e0,#d84a4a)"></div><div class="tile-label">Fitness<br>Programs<br><span class="stars">★★★★<i>★</i></span></div></div>
</section>

<section class="abs points">
  <div class="point" style="left:126px">
    <div class="point-icon"><svg width="22" height="34" viewBox="0 0 22 34"><rect x="1" y="1" width="20" height="32" rx="3" fill="#fff"/><rect x="4" y="5" width="14" height="20" fill="#4fa4d2"/><circle cx="11" cy="29" r="1.8" fill="#4fa4d2"/></svg></div>
    <p class="point-text">Listen on your Zarno,<br>Tavo or Droidal device</p>
  </div>
  <div class="point" style="left:344px">
    <div class="point-icon"><svg width="36" height="36" viewBox="0 0 36 36"><path d="M20 4h11v11L15 31 4 20z" fill="#fff"/><circle cx="26" cy="10" r="2.5" fill="#4fa4d2"/><text x="15" y="23" font-family="Open Sans,sans-serif" font-size="12" font-weight="700" fill="#4fa4d2" transform="rotate(-45 15 19)">$</text></svg></div>
    <p class="point-text">All you can enjoy for<br>one low monthly price</p>
  </div>
  <div class="point" style="left:564px">
    <div class="point-icon"><svg width="36" height="36" viewBox="0 0 36 36"><circle cx="18" cy="18" r="17" fill="#fff"/><path d="M12 12l12 12M24 12L12 24" stroke="#4fa4d2" stroke-width="4" stroke-linecap="round"/></svg></div>
    <p class="point-text">No obligation. Cancel<br>any time</p>
  </div>
</section>

<section class="abs signup">
  <h2 class="abs signup-title" style="font-weight:400">Start Your Free Trial</h2>
  <p class="abs signup-copy">You will get instant &amp; unlimited access to all the material on Dunmoral for 14 days. There is no obligation &amp; you can cancel at any time.</p>
  <p class="abs signup-note">Credit Card Not Required for Free Trial</p>
  <div class="abs email">Your Email Address</div>
  <div class="abs access">Get Instant Access</div>
  <div class="abs or">OR</div>
  <div class="abs chatterly"><span class="chatterly-sq"></span>Sign up with Chatterly</div>
</section>

<footer class="abs footer">
  <p class="abs footer-links">About | Help | Contact Us | Member Login | Privacy Policy | Terms of Service</p>
  <p class="abs copyright">©2014 Dunmoral LLC - All Rights Reserved</p>
</footer>
</body>
</html>
```